Upmarket Dessert Lounge needs a Business Card Design

We are an upmarket dessert lounge needing a business card to match our image.

We want something that is simple yet beautiful, feminine, classy, sophisticated and elegant. We want it to stand out and don't mind if it is bold.

The design should include our logo and colours of red or maroon with gold highlights. We don't mind if black is used.

Marlow & Quince

Target Market(s)

For those who like to indulge or treat themselves and give in to their temptations on good quality desserts.

Industry/Entity Type

Business

Requirements
Must have
• Must include our logo and our name

Marlow & Quince

M & Q

```html
<!DOCTYPE html>
<html lang="en">
<head>
<meta charset="utf-8">
<title>Marlow &amp; Quince — Business Card</title>
<link rel="stylesheet" href="https://fonts.googleapis.com/css2?family=Libre+Baskerville&display=swap">
<style>
  :root {
    --backdrop: #5d7480;
    --card-red: #7e2420;
    --card-red-light: #8c2c27;
    --card-red-dark: #6f1d1a;
    --gold: #f2d9a0;
    --gold-soft: rgba(242, 217, 160, 0.18);
    --card-shadow: rgba(20, 30, 36, 0.35);
  }
  * { margin: 0; padding: 0; box-sizing: border-box; }
  html, body {
    width: 1200px;
    height: 960px;
    overflow: hidden;
    background: var(--backdrop);
    font-family: "Libre Baskerville", "Times New Roman", serif;
    color: var(--gold);
  }
  .stage {
    position: relative;
    width: 1200px;
    height: 960px;
  }
  .card {
    position: absolute;
    left: 240px;
    width: 720px;
    height: 411px;
    background: linear-gradient(160deg, var(--card-red-light), var(--card-red) 55%, var(--card-red-dark));
    box-shadow: 0 14px 30px var(--card-shadow);
  }
  .card--front { top: 50px; }
  .card--back { top: 500px; }

  /* Front */
  .monogram {
    position: absolute;
    left: 52px;
    top: 62px;
    width: 250px;
    height: 160px;
    display: flex;
    align-items: center;
    justify-content: center;
    gap: 14px;
  }
  .monogram__dot {
    width: 12px;
    height: 12px;
    border-radius: 50%;
    background: var(--gold);
  }
  .monogram__text {
    font-size: 64px;
    line-height: 1;
  }
  .flourish {
    position: absolute;
    right: 20px;
    top: 145px;
    width: 190px;
    height: 105px;
    border-radius: 60px 10px 60px 10px;
    background: radial-gradient(ellipse at center, rgba(90, 18, 16, 0.45), rgba(90, 18, 16, 0));
  }
  .person {
    position: absolute;
    left: 395px;
    top: 98px;
  }
  .person__name { font-size: 27px; }
  .person__role { font-size: 15px; margin-top: 12px; }
  .divider {
    position: absolute;
    left: 52px;
    right: 28px;
    top: 262px;
    height: 2px;
    background: var(--gold);
  }
  .contact-list {
    position: absolute;
    left: 52px;
    top: 290px;
    list-style: none;
    font-size: 17px;
    line-height: 31px;
  }
  .contact-list li { display: flex; align-items: center; gap: 14px; }
  .contact-list svg { width: 18px; height: 18px; flex: none; }
  .address {
    position: absolute;
    left: 408px;
    top: 290px;
    font-size: 15px;
    line-height: 27px;
    font-style: normal;
  }

  /* Back */
  .pattern {
    position: absolute;
    inset: 0;
    background: linear-gradient(160deg, var(--card-red-light), var(--card-red));
  }
  .ornament-band {
    position: absolute;
    left: 115px;
    top: 95px;
    width: 490px;
    height: 220px;
    border-radius: 110px;
    background: radial-gradient(ellipse at center, var(--gold-soft), rgba(242, 217, 160, 0));
  }
  .brand-name {
    position: absolute;
    left: 0;
    right: 0;
    top: 182px;
    text-align: center;
    font-size: 40px;
    letter-spacing: 2px;
    line-height: 1;
  }
</style>
</head>
<body>
<main class="stage">

  <section class="card card--front" aria-label="Business card front">
    <div class="monogram">
      <span class="monogram__dot"></span>
      <span class="monogram__text">M &amp; Q</span>
    </div>
    <div class="flourish" role="img" aria-label="Faint floral flourish decoration"></div>

    <div class="person">
      <p class="person__name">Name Surname</p>
      <p class="person__role">Manager</p>
    </div>

    <div class="divider"></div>

    <ul class="contact-list">
      <li>
        <svg viewBox="0 0 18 18" aria-hidden="true"><rect x="2" y="1" width="14" height="16" rx="1.5" fill="none" stroke="currentColor" stroke-width="1.6"/><rect x="5" y="3.5" width="3" height="11" fill="currentColor"/><rect x="10" y="4" width="4" height="2" fill="currentColor"/><rect x="10" y="8" width="4" height="2" fill="currentColor"/><rect x="10" y="12" width="4" height="2" fill="currentColor"/></svg>
        <span>(555) 01 842 63 17</span>
      </li>
      <li>
        <svg viewBox="0 0 18 18" aria-hidden="true"><rect x="5" y="1" width="8" height="5" fill="none" stroke="currentColor" stroke-width="1.6"/><rect x="1" y="6" width="16" height="8" rx="1.5" fill="currentColor"/><rect x="5" y="11" width="8" height="6" fill="var(--card-red)" stroke="currentColor" stroke-width="1.6"/></svg>
        <span>(555) 01 842 63 18</span>
      </li>
      <li>
        <svg viewBox="0 0 18 18" aria-hidden="true"><rect x="1" y="3.5" width="16" height="11" fill="none" stroke="currentColor" stroke-width="1.6"/><path d="M1 3.5 L9 10 L17 3.5 M1 14.5 L7 8.5 M17 14.5 L11 8.5" fill="none" stroke="currentColor" stroke-width="1.4"/></svg>
        <span>info@marlowquince.com</span>
      </li>
    </ul>

    <address class="address">
      Rue des Tilleuls - Les Pins<br>
      BP 218 - City, Country<br>
      www.marlowquince.com
    </address>
  </section>

  <section class="card card--back" aria-label="Business card back">
    <div class="pattern" role="img" aria-label="Subtle diamond lattice pattern"></div>
    <div class="ornament-band" role="img" aria-label="Ornate scrollwork frame decoration"></div>
    <p class="brand-name">MARLOW &amp; QUINCE</p>
  </section>

</main>
</body>
</html>
```